New Business Card Design for Manufacturing

We are an engineering/manufacturing company that offers Advanced machining/assembly/engineering services, as well as innovative products for the heavy duty engine cooling markets.

We are looking to get a new business card designed that is clean and modern looking, but still fits the wide range of technical/skilled work we do.

- We hope to use this design as the base for other design work in new Presentations, web, and print work.

Industry/Entity Type

Engineering

Contact Information for Business Card

Our preferred color of blue is (RGB) 22/71/159 but can vary slightly from that color. Our content will be our Logo and full company name (Vantrell Forge Works, Inc.), company address, name, job title, phone number with extension, cell number, fax number, website, and email address on the cards.
We'd like the full company name next to the logo, but we are open to other interpretations of that layout.
Preferably, we would like the back side to be clean with just our logo, and the front to contain all of the contact information.

Colors
2f74b4
0355a3
85abd2

Requirements
Must have
• - Logo, company name, needed content - We are open to interpretation beyond that.
• - Standard size business card.
• - Horizontal orientation.
• - Enough space for lengthy names / job titles (for example, a job title could read "Directory of Human Resources" or "V.P. of Governmental Affairs"). We need this to look clean, whether the title be short (CEO) or long (as described above).

```html
<!DOCTYPE html>
<html lang="en">
<head>
<meta charset="utf-8">
<title>Vantrell Forge Works – Business Card</title>
<link href="https://fonts.googleapis.com/css2?family=Open+Sans:wght@400;600;800&display=swap" rel="stylesheet">
<style>
  :root {
    --brand-blue: #16479f;
    --deep-blue: #0d3a8a;
    --mid-blue: #2f74b4;
    --light-blue: #85abd2;
    --card-white: #f4f5f7;
    --page-bg: #2a2b2e;
  }
  * { box-sizing: border-box; margin: 0; padding: 0; }
  html, body { width: 1200px; height: 1200px; overflow: hidden; }
  body {
    background: var(--page-bg);
    font-family: "Open Sans", sans-serif;
    display: flex;
    flex-direction: column;
    align-items: center;
    justify-content: center;
    gap: 60px;
  }
  .card {
    position: relative;
    width: 880px;
    height: 503px;
    overflow: hidden;
    border-radius: 4px;
    box-shadow: 0 10px 30px rgba(0,0,0,.45);
  }

  /* Front */
  .card-front { background: var(--card-white); color: var(--brand-blue); }
  .top-rule {
    position: absolute; left: 0; right: 0; top: 30px;
    height: 6px; background: var(--brand-blue);
  }
  .brand-name {
    position: absolute; left: 330px; top: 66px;
    font-weight: 800; font-size: 62px; letter-spacing: 1px;
    color: var(--brand-blue); line-height: 1;
  }
  .company-name {
    position: absolute; left: 660px; top: 64px;
    font-weight: 800; font-size: 25px; line-height: 1.02;
    text-transform: uppercase; color: var(--brand-blue);
  }
  .company-name small { font-size: 13px; }
  .name-tab {
    position: absolute; left: 0; top: 120px;
    width: 320px; height: 92px;
    background: var(--brand-blue);
    border-radius: 0 46px 46px 0;
    color: #fff; padding: 14px 0 0 40px;
  }
  .name-tab .person { font-weight: 600; font-size: 22px; line-height: 1.2; }
  .name-tab .title { font-size: 16px; }
  .divider {
    position: absolute; left: 320px; right: 0; top: 200px;
    height: 7px; background: var(--brand-blue);
  }
  .contact {
    position: absolute; right: 110px; top: 234px;
    text-align: right; font-size: 16px; line-height: 1.3;
    color: var(--brand-blue);
  }
  .contact-group { margin-bottom: 10px; }
  .connectors { position: absolute; right: 0; top: 226px; }
  .footer-band {
    position: absolute; left: 0; right: 0; bottom: 0; height: 76px;
    background: var(--brand-blue);
    display: flex; align-items: center; padding-left: 40px;
  }
  .website { color: #fff; font-weight: 800; font-size: 26px; }

  /* Back */
  .card-back { display: flex; align-items: center; justify-content: center; }
  .back-texture {
    position: absolute; inset: 0;
    background: radial-gradient(ellipse at 45% 45%, var(--mid-blue) 0%, var(--brand-blue) 55%, var(--deep-blue) 100%);
  }
  .back-mark {
    position: relative;
    font-weight: 800; font-size: 110px; letter-spacing: 3px;
    color: #fff;
  }
</style>
</head>
<body>

  <section class="card card-front" aria-label="Business card front">
    <div class="top-rule"></div>
    <div class="brand-name">VANTRELL</div>
    <div class="company-name">Vantrell<br>Forge<br>Works <small>Inc</small></div>

    <div class="name-tab">
      <div class="person">Full Name</div>
      <div class="title">Office</div>
    </div>
    <div class="divider"></div>

    <div class="contact">
      <div class="contact-group">
        Tel. +1 555 0142 7730<br>
        Fax. +1 555 0142 7731<br>
        Fax. +1 555 0142 7732
      </div>
      <div class="contact-group">info@vantrellforge.com</div>
      <div class="contact-group">
        VANTRELL FORGE WORKS<br>
        418 Harlow Street - Suite 2<br>
        Dunmore - USA
      </div>
    </div>

    <svg class="connectors" width="110" height="190" viewBox="0 0 110 190" aria-hidden="true">
      <g fill="none" stroke="var(--brand-blue)" stroke-width="3" stroke-linecap="round">
        <!-- phone -->
        <path d="M16 30c0 10 8 18 18 18l3-5-5-3-2 2c-4-2-7-5-9-9l2-2-3-5z" fill="var(--brand-blue)" stroke="none"/>
        <line x1="60" y1="38" x2="110" y2="38"/>
        <!-- mail -->
        <rect x="14" y="88" width="24" height="17" rx="2"/>
        <path d="M14 90l12 9 12-9"/>
        <line x1="60" y1="96" x2="110" y2="96"/>
        <!-- pin -->
        <path d="M26 160c-8-10-11-15-11-20a11 11 0 0 1 22 0c0 5-3 10-11 20z" fill="var(--brand-blue)" stroke="none"/>
        <circle cx="26" cy="140" r="4" fill="#fff" stroke="none"/>
        <line x1="60" y1="150" x2="110" y2="150"/>
      </g>
      <g fill="var(--brand-blue)">
        <circle cx="60" cy="38" r="6"/>
        <circle cx="60" cy="96" r="6"/>
        <circle cx="60" cy="150" r="6"/>
      </g>
    </svg>

    <div class="footer-band">
      <span class="website">www.vantrellforge.com</span>
    </div>
  </section>

  <section class="card card-back" aria-label="Business card back">
    <div class="back-texture" role="img" aria-label="Soft blue abstract network texture"></div>
    <div class="back-mark">VANTRELL</div>
  </section>

</body>
</html>
```